Request for Business Card Design

Hi. My name is Marlene, I am looking for a new business card design for my company, Quarrow Signal Instruments, LLC. I really like the design you did for Tarsel Venture and was hoping you could do something similar using our full logo and our mark. I am also open to any raised texture design using our mark. I have attached our full logo, which would need to be somewhere on the card, as well as the mark in both outline and full form, as well as our brand colors / guide. The card does not have to be white, as long as our logo and mark appear. I actually like darker colored business cards more, but am open to all options. If you are interested in working with me, please let me know. We would also take the business card design into letterhead design if you can do that.

```html
<!DOCTYPE html>
<html lang="en">
<head>
<meta charset="utf-8">
<title>Quarrow Signal Instruments — Business Card</title>
<link rel="stylesheet" href="https://fonts.googleapis.com/css2?family=Open+Sans:wght@400;600;700;800&display=swap">
<style>
  :root {
    --backdrop: #1b1b1d;
    --card-dark: #38383b;
    --card-shade: #2b2b2e;
    --brand-blue: #1b95c4;
    --paper-white: #f4f4f4;
    --text-light: #ffffff;
    --text-soft: #e6e6e6;
  }
  * { margin: 0; padding: 0; box-sizing: border-box; }
  html, body {
    width: 1200px; height: 780px; overflow: hidden;
    background: var(--backdrop);
    font-family: "Open Sans", Arial, sans-serif;
  }
  .canvas {
    position: relative; width: 1200px; height: 780px;
    display: flex; align-items: center; justify-content: center; gap: 60px;
  }
  .card {
    position: relative; width: 520px; height: 300px;
    overflow: hidden; border-radius: 3px;
    box-shadow: 0 10px 30px rgba(0,0,0,.45);
  }

  /* Front */
  .card-front { background: var(--card-dark); color: var(--text-light); }
  .front-swoosh { position: absolute; inset: 0; width: 100%; height: 100%; }
  .wordmark { position: absolute; left: 28px; top: 24px; display: flex; align-items: center; gap: 12px; }
  .wordmark-dot { width: 36px; height: 36px; border-radius: 50%; background: var(--brand-blue); }
  .wordmark-name { font-weight: 800; font-size: 30px; letter-spacing: 3px; line-height: 1; }
  .wordmark-tagline { font-weight: 800; font-size: 8px; letter-spacing: 1px; margin-top: 4px; }
  .address {
    position: absolute; left: 34px; top: 108px;
    font-size: 12.5px; line-height: 1.45; color: var(--text-soft);
  }
  .person { position: absolute; right: 34px; top: 142px; text-align: right; }
  .person-name { font-weight: 700; font-size: 32px; color: var(--brand-blue); line-height: 1; }
  .person-role { font-size: 15px; margin-top: 2px; }
  .edge-tab { position: absolute; right: 0; top: 184px; width: 14px; height: 52px; background: var(--brand-blue); }
  .contacts {
    position: absolute; right: 28px; top: 210px; list-style: none;
    font-size: 12.5px; line-height: 19px; color: var(--text-soft);
  }
  .contacts li { display: flex; justify-content: flex-end; align-items: center; gap: 8px; }
  .contacts svg { width: 12px; height: 12px; fill: var(--brand-blue); }

  /* Back */
  .card-back { background: var(--card-shade); }
  .texture-field {
    position: absolute; inset: 0;
    background: linear-gradient(115deg, #252528 0%, #2f2f32 45%, #4a4a4d 75%, #8a8a8c 100%);
  }
  .back-wordmark { position: absolute; right: 70px; bottom: 40px; display: flex; align-items: center; gap: 8px; color: var(--text-light); }
  .back-wordmark .wordmark-dot { width: 20px; height: 20px; }
  .back-wordmark .wordmark-name { font-size: 16px; letter-spacing: 1.5px; }
  .back-wordmark .wordmark-tagline { font-size: 5px; letter-spacing: .5px; margin-top: 2px; }
</style>
</head>
<body>
<main class="canvas">

  <section class="card card-front" aria-label="Business card front">
    <svg class="front-swoosh" viewBox="0 0 520 300" aria-hidden="true">
      <path d="M0 142 C130 170 270 220 350 300 L0 300 Z" fill="var(--brand-blue)"/>
      <path d="M0 160 C130 190 250 240 310 300 L0 300 Z" fill="#232325"/>
      <path d="M0 172 C150 200 330 240 430 300 L0 300 Z" fill="var(--card-dark)" opacity="0"/>
      <path d="M0 178 C110 200 230 246 300 300 L0 300 Z" fill="var(--brand-blue)"/>
      <path d="M0 200 C90 215 200 250 280 300 L0 300 Z" fill="var(--paper-white)"/>
    </svg>

    <div class="wordmark">
      <span class="wordmark-dot"></span>
      <div>
        <div class="wordmark-name">QUARROW</div>
        <div class="wordmark-tagline">SIGNAL INSTRUMENTS</div>
      </div>
    </div>

    <p class="address">1180 Harlow Mill Road,<br>Tressbury, CO 80611</p>

    <div class="person">
      <div class="person-name">Marlene</div>
      <div class="person-role">Director</div>
    </div>
    <span class="edge-tab"></span>

    <ul class="contacts">
      <li>+001 555 214 3380
        <svg viewBox="0 0 24 24"><path d="M6.6 10.8a15 15 0 0 0 6.6 6.6l2.2-2.2a1 1 0 0 1 1-.25 11.4 11.4 0 0 0 3.6.57 1 1 0 0 1 1 1V20a1 1 0 0 1-1 1A17 17 0 0 1 3 4a1 1 0 0 1 1-1h3.5a1 1 0 0 1 1 1c0 1.25.2 2.45.57 3.57a1 1 0 0 1-.25 1z"/></svg></li>
      <li>+001 555 214 3391
        <svg viewBox="0 0 24 24"><path d="M6 3h9v5H6zM4 9h16a1 1 0 0 1 1 1v10a1 1 0 0 1-1 1H4a1 1 0 0 1-1-1V10a1 1 0 0 1 1-1zm3 3v2h2v-2zm4 0v2h2v-2zm4 0v2h2v-2zm-8 4v2h2v-2zm4 0v2h2v-2z"/></svg></li>
      <li>www.quarrowsignal.com
        <svg viewBox="0 0 24 24"><path d="M12 2a10 10 0 1 0 0 20 10 10 0 0 0 0-20zm6.9 6h-3a15 15 0 0 0-1.3-3.9A8 8 0 0 1 18.9 8zM12 4c.8 1.2 1.5 2.5 1.9 4h-3.8c.4-1.5 1.1-2.8 1.9-4zM4.3 14a8 8 0 0 1 0-4h3.4a16 16 0 0 0 0 4zm.8 2h3a15 15 0 0 0 1.3 3.9A8 8 0 0 1 5.1 16zm3-8h-3a8 8 0 0 1 4.3-3.9A15 15 0 0 0 8.1 8zM12 20c-.8-1.2-1.5-2.5-1.9-4h3.8c-.4 1.5-1.1 2.8-1.9 4zm2.3-6H9.7a14 14 0 0 1 0-4h4.6a14 14 0 0 1 0 4zm.3 5.9a15 15 0 0 0 1.3-3.9h3a8 8 0 0 1-4.3 3.9zm1.7-5.9a16 16 0 0 0 0-4h3.4a8 8 0 0 1 0 4z"/></svg></li>
      <li>info@quarrowsignal.com
        <svg viewBox="0 0 24 24"><path d="M3 5h18a1 1 0 0 1 1 1v12a1 1 0 0 1-1 1H3a1 1 0 0 1-1-1V6a1 1 0 0 1 1-1zm1 2.4V17h16V7.4l-8 5.3z M4.6 7 12 11.9 19.4 7z"/></svg></li>
    </ul>
  </section>

  <section class="card card-back" aria-label="Business card back">
    <div class="texture-field" role="img" aria-label="Raised repeating brand-mark texture across the card, fading from dark to light grey"></div>
    <div class="back-wordmark">
      <span class="wordmark-dot"></span>
      <div>
        <div class="wordmark-name">QUARROW</div>
        <div class="wordmark-tagline">SIGNAL INSTRUMENTS</div>
      </div>
    </div>
  </section>

</main>
</body>
</html>
```